Redesign existing company profile, brochure, and design 5 individual product sheets.

Competition entrants are required to provide a sample of the designs for the company profile, brochure and product sheets. The competition winner will then provide completed versions of all documents in InDesign format, including all text layout to create completed documents.

We require our company profile (12 pages) and brochure (4 pages) redesigned so that there is a consistent, professional theme throughout. We also have 5 word documents of text we would like made into individual product sheets following the same theme to be designed for the company profile and brochure.
Ideal candidate should have advanced InDesign skills, exceptional eye for detail and graphic design experience.

What we want done:

Company Profile:
• Redesign our existing company profile using Adobe InDesign. (pdf of existing profile attached).
• Replace the existing images with new images consistent with the new design. (We can pay for stock images used).
• Update logos (new logo attached), also make sure the colours used match our logo colours (CMYK guide attached).
• Create consistency with themes, colours and fonts throughout the brochure, company profile and product sheets.

Brochure:
• Redesign our existing brochure using Adobe InDesign. (pdf of existing brochure attached).
• Make sure the colours used match our logo colours (CMYK guide attached).

Product Sheets:
• Design 5 new A4 double sided product sheets using the text provided.

```html
<!DOCTYPE html>
<html lang="en">
<head>
<meta charset="utf-8">
<title>Calderway Managed IT Services – Brochure</title>
<link rel="stylesheet" href="https://fonts.googleapis.com/css2?family=Montserrat:ital,wght@0,300;0,400;0,500;0,600;0,700;1,400&family=Open+Sans:wght@400;600&display=swap">
<style>
  :root{
    --red:#e63a35;
    --red-deep:#c92d29;
    --grey:#8e8e90;
    --grey-light:#ececed;
    --ink:#4d4d4f;
    --paper:#ffffff;
    --backdrop:#e4e4e6;
  }
  *{box-sizing:border-box;margin:0;padding:0}
  html,body{width:1200px;height:3360px;overflow:hidden}
  body{background:var(--backdrop);position:relative;font-family:"Open Sans",Arial,sans-serif;color:var(--ink)}
  .heading{font-family:"Montserrat",Arial,sans-serif}

  /* ---------- cover ---------- */
  .cover{position:absolute;overflow:hidden;background:var(--paper);box-shadow:0 6px 22px rgba(0,0,0,.12)}
  .cover--solo{left:180px;top:70px;width:840px;height:1188px;font-size:20px}
  .cover--spread{left:600px;top:1338px;width:560px;height:792px;font-size:13.333px;box-shadow:none}
  .cover-photo{position:absolute;inset:0;background:linear-gradient(165deg,#e3edf8 0%,#b3c9e2 22%,#7d98b8 45%,#4c6582 68%,#2b3a4d 100%)}
  .cover-band{position:absolute;left:0;top:0;width:34%;height:100%;background:var(--red)}
  .cover-tab{position:absolute;left:0;top:4%;width:34%;height:7%;background:var(--grey)}
  .cover-arrow{position:absolute;left:38%;top:4.6%;width:2.4em;height:2.4em}
  .cover-brand{position:absolute;left:7%;top:16%;height:44%;writing-mode:vertical-rl;transform:rotate(180deg);color:#fff;font-family:"Montserrat",Arial,sans-serif;font-weight:500;display:flex;align-items:center;gap:.6em}
  .cover-brand .brand-square{display:block;width:2.6em;height:2.6em;background:#fff}
  .cover-brand .brand-name{font-size:2.3em;letter-spacing:.06em;line-height:1}
  .cover-brand .brand-sub{font-size:1.05em;letter-spacing:.14em;line-height:1}
  .cover-rule{position:absolute;left:27%;top:70%;width:2px;height:20%;background:#fff}
  .cover-tagline{position:absolute;right:6%;top:8%;width:34%;text-align:right;color:#fff;font-size:.8em;line-height:1.4}
  .cover-contact{position:absolute;left:41%;top:71%;color:#fff;font-size:.85em;line-height:1.9}
  .cover-contact .contact-title{font-family:"Montserrat",Arial,sans-serif;font-weight:300;font-size:2em;letter-spacing:.18em;margin-bottom:.5em}

  /* ---------- pages ---------- */
  .page{position:absolute;width:560px;height:792px;background:var(--paper);overflow:hidden}
  .spread{position:absolute;left:40px;width:1120px;height:792px;box-shadow:0 6px 22px rgba(0,0,0,.12)}
  .spread--outer{top:1338px}
  .spread--inner{top:2210px}
  .spread::after{content:"";position:absolute;left:559px;top:0;width:2px;height:100%;background:rgba(0,0,0,.07);z-index:5}

  /* back cover */
  .back-contact{position:absolute;left:32px;top:20px;color:var(--red);font-size:11px;line-height:1.5;font-weight:600}
  .back-brand{position:absolute;right:28px;top:22px;display:flex;align-items:center;gap:8px;color:var(--red);font-family:"Montserrat",Arial,sans-serif;font-weight:600;font-size:15px;letter-spacing:.05em}
  .back-brand .brand-square{width:18px;height:18px;background:var(--red)}
  .back-photo{position:absolute;right:0;top:72px;width:76%;height:290px;background:radial-gradient(circle at 55% 55%,#cfe6ff 0%,#4c8fd6 18%,#173a66 48%,#070d1a 100%)}
  .back-lead{position:absolute;left:0;top:176px;width:52%;height:52px;background:var(--grey);color:#fff;font-family:"Montserrat",Arial,sans-serif;font-weight:500;font-size:11px;letter-spacing:.08em;line-height:1.35;padding:9px 0 0 32px}
  .back-panel{position:absolute;left:0;top:228px;width:58%;height:210px;background:var(--red);color:#fff;padding:18px 26px 0 32px}
  .back-panel .services{font-family:"Montserrat",Arial,sans-serif;font-weight:500;font-size:13px;line-height:1.45}
  .back-panel .quote{margin-top:16px;font-size:12.5px;line-height:1.45;font-style:italic}
  .back-copy{position:absolute;left:32px;top:470px;width:496px;font-size:10.5px;line-height:1.6;color:#6a6a6c}

  /* inner left */
  .intro-tab{position:absolute;left:0;top:0;width:30%;height:70px;background:var(--red);color:#fff;font-size:10px;line-height:1.45;padding:14px 16px}
  .meeting-photo{position:absolute;left:0;top:70px;width:56%;height:200px;background:linear-gradient(135deg,#f2f4f6 0%,#c9d0d8 40%,#6c7480 75%,#2d3138 100%)}
  .services-head{position:absolute;left:56%;top:78px;width:44%;height:38px;background:var(--grey);color:#fff;font-family:"Montserrat",Arial,sans-serif;font-weight:500;font-size:15px;letter-spacing:.12em;padding:10px 0 0 22px}
  .services-list{position:absolute;left:60%;top:132px;width:36%}
  .services-list .lead{color:var(--red);font-weight:600;font-size:11.5px;line-height:1.4;margin-bottom:8px}
  .services-list ul{list-style:none;font-size:10.5px;line-height:1.6}
  .services-list li::before{content:"";display:inline-block;width:5px;height:5px;background:var(--red);margin-right:7px;vertical-align:middle}
  .cloud-band{position:absolute;left:0;top:290px;width:100%;height:160px;background:var(--grey-light);padding:18px 32px}
  .cloud-band::after{content:"";position:absolute;right:0;top:0;width:38%;height:26px;background:var(--grey)}
  .section-title{font-family:"Montserrat",Arial,sans-serif;font-weight:600;font-size:12.5px;letter-spacing:.06em;color:var(--red);margin-bottom:6px}
  .cloud-band .section-title{color:var(--ink)}
  .body-copy{font-size:10.5px;line-height:1.55}
  .cloud-band ul{list-style:none;font-size:10.5px;line-height:1.55;margin-top:6px}
  .cloud-band li::before{content:"– "}
  .promise-tab{position:absolute;left:0;top:472px;width:22%;height:180px;background:var(--red);color:#fff;font-size:10px;line-height:1.5;padding:16px 14px}
  .promise{position:absolute;left:27%;top:478px;width:66%}
  .partners{position:absolute;left:27%;top:570px;width:66%}
  .partner-row{display:flex;gap:18px;margin-top:12px;align-items:center}
  .partner-badge{width:92px;height:34px;background:#d5d5d7;border-radius:3px}
  .partner-badge--round{width:34px;border-radius:50%}

  /* inner right */
  .client-quote{position:absolute;left:44px;top:36px;width:472px;color:var(--red);font-style:italic;font-family:"Montserrat",Arial,sans-serif;font-size:12px;line-height:1.5}
  .managed{position:absolute;left:44px;top:112px;width:300px}
  .benefits{position:absolute;left:366px;top:140px;width:166px;height:310px;background:var(--grey-light);padding:16px 14px}
  .benefits .section-title{font-size:12px;line-height:1.3;margin-bottom:10px}
  .benefits ul{list-style:none;font-size:10px;line-height:1.5}
  .benefits li{display:flex;gap:6px;margin-bottom:3px}
  .benefits li svg{flex:none;margin-top:3px}
  .monthly{position:absolute;left:44px;top:268px;width:300px}
  .plans{position:absolute;left:44px;top:420px;width:488px;display:flex;justify-content:space-between}
  .plan{width:140px;text-align:center}
  .plan-badge{width:46px;height:46px;border:2.5px solid var(--red);border-radius:50%;margin:0 auto 10px;display:flex;align-items:center;justify-content:center;color:var(--red);font-family:"Montserrat",Arial,sans-serif;font-weight:700;font-size:18px}
  .plan p{font-size:10px;line-height:1.45}
  .people{position:absolute;left:44px;top:600px;width:488px}
  .pricing{position:absolute;left:44px;top:690px;width:488px}
</style>
</head>
<body>

<!-- front cover -->
<section class="cover cover--solo">
  <div class="cover-photo" role="img" aria-label="Photograph looking up at a glass office tower against a blue cloudy sky"></div>
  <div class="cover-band"></div>
  <div class="cover-tab"></div>
  <svg class="cover-arrow" viewBox="0 0 40 40" fill="none" stroke="#fff" stroke-width="1.6"><path d="M6 10 L20 26 L34 10"/><path d="M20 2 V26"/><path d="M4 34 H36"/></svg>
  <div class="cover-brand"><span class="brand-square"></span><span class="brand-name">CALDERWAY</span><span class="brand-sub">MANAGED IT SERVICES</span></div>
  <div class="cover-rule"></div>
  <p class="cover-tagline">Lorem ipsum dolor sit amet, consectetur adipiscing elit</p>
  <div class="cover-contact">
    <p class="contact-title">CONTACT</p>
    <p>1300 482 615</p>
    <p>hello@calderway.com.au</p>
    <p>calderway.com.au</p>
  </div>
</section>

<!-- outer spread: back + front -->
<section class="spread spread--outer">
  <article class="page" style="left:0;top:0">
    <div class="back-contact">www.calderway.com.au<br>1300 482 615</div>
    <div class="back-brand"><span class="brand-square"></span>CALDERWAY</div>
    <div class="back-photo" role="img" aria-label="Illustration of a glowing digital globe held above an open hand"></div>
    <div class="back-lead">RESPONSIVE,<br>ENLIGHTENING &amp; EMPOWERING</div>
    <div class="back-panel">
      <p class="services">Managed IT Services • Cloud Solutions • Remote &amp; Onsite Support • Project Management • Consulting • IT Support • Sydney based Help Desk</p>
      <p class="quote">“We believe that the right IT platforms and support can help all businesses grow and expand their capabilities” (Daniel Harrow, Founder &amp; Principal Consultant)</p>
    </div>
    <p class="back-copy">We provide tailored managed IT services for clients who need a responsive, experienced and caring partner. We are fully committed to keeping our clients ahead with reliable, secure and productive technology, so their teams can focus on the work that matters. Our Sydney based help desk, proactive monitoring and onsite engineers give every business the confidence to grow, knowing that expert support is always a phone call away.</p>
  </article>
  <section class="cover cover--spread" style="left:560px;top:0">
    <div class="cover-photo" role="img" aria-label="Photograph looking up at a glass office tower against a blue cloudy sky"></div>
    <div class="cover-band"></div>
    <div class="cover-tab"></div>
    <svg class="cover-arrow" viewBox="0 0 40 40" fill="none" stroke="#fff" stroke-width="1.6"><path d="M6 10 L20 26 L34 10"/><path d="M20 2 V26"/><path d="M4 34 H36"/></svg>
    <div class="cover-brand"><span class="brand-square"></span><span class="brand-name">CALDERWAY</span><span class="brand-sub">MANAGED IT SERVICES</span></div>
    <div class="cover-rule"></div>
    <p class="cover-tagline">Lorem ipsum dolor sit amet, consectetur adipiscing elit</p>
    <div class="cover-contact">
      <p class="contact-title">CONTACT</p>
      <p>1300 482 615</p>
      <p>hello@calderway.com.au</p>
      <p>calderway.com.au</p>
    </div>
  </section>
</section>

<!-- inner spread -->
<section class="spread spread--inner">
  <article class="page" style="left:0;top:0">
    <div class="intro-tab">Lorem ipsum dolor sit amet, consectetur adipiscing elit</div>
    <div class="meeting-photo" role="img" aria-label="Photograph of business colleagues reviewing documents at a meeting table"></div>
    <h2 class="services-head heading">OUR SERVICES</h2>
    <div class="services-list">
      <p class="lead">We take care of all your IT needs. Our services include:</p>
      <ul>
        <li>Cloud Solutions</li>
        <li>Managed IT Services</li>
        <li>IT Support – Onsite and Remote</li>
        <li>Internet Connectivity</li>
        <li>Backup &amp; Recovery Solutions</li>
        <li>Project Management</li>
        <li>Specialist Consulting</li>
      </ul>
    </div>
    <div class="cloud-band">
      <h3 class="section-title">CLOUD SOLUTIONS</h3>
      <p class="body-copy" style="width:62%">We specialise in moving businesses to tailored cloud platforms, giving your team secure access from anywhere. As a certified partner we offer clients a range of options:</p>
      <ul>
        <li>Cloud Hosted Servers</li>
        <li>Office Productivity Suites</li>
        <li>Cloud Backup Services</li>
        <li>Hybrid Cloud Solutions</li>
      </ul>
    </div>
    <div class="promise-tab">Lorem ipsum dolor sit amet, consectetur adipiscing elit, sed do eiusmod tempor.</div>
    <div class="promise">
      <h3 class="section-title">OUR PROMISE</h3>
      <p class="body-copy">We will work in partnership to understand your requirements and provide the right solutions that will empower you to be more productive and help your business grow.</p>
    </div>
    <div class="partners">
      <h3 class="section-title">OUR PARTNERS</h3>
      <p class="body-copy">We work with leading technology vendors.</p>
      <div class="partner-row">
        <span class="partner-badge"></span>
        <span class="partner-badge partner-badge--round"></span>
        <span class="partner-badge"></span>
      </div>
    </div>
  </article>

  <article class="page" style="left:560px;top:0">
    <p class="client-quote">“We are flexible, customer focused and committed to understanding client requirements. We enable clients to fulfil their business ambitions.”</p>
    <div class="managed">
      <h3 class="section-title">MANAGED IT SERVICES</h3>
      <p class="body-copy">Our managed services are at the core of our tailored solutions. We monitor, maintain and protect your systems so issues are resolved before they affect your staff, with clear reporting and a single point of contact.</p>
    </div>
    <aside class="benefits">
      <h3 class="section-title">MANAGED SERVICE PLAN BENEFITS</h3>
      <ul>
        <li><svg width="9" height="9" viewBox="0 0 10 10"><path d="M1 5 L4 8 L9 1" fill="none" stroke="#e63a35" stroke-width="2"/></svg>Predictable monthly costs</li>
        <li><svg width="9" height="9" viewBox="0 0 10 10"><path d="M1 5 L4 8 L9 1" fill="none" stroke="#e63a35" stroke-width="2"/></svg>24/7 monitoring of all key services</li>
        <li><svg width="9" height="9" viewBox="0 0 10 10"><path d="M1 5 L4 8 L9 1" fill="none" stroke="#e63a35" stroke-width="2"/></svg>Proactive security updates</li>
        <li><svg width="9" height="9" viewBox="0 0 10 10"><path d="M1 5 L4 8 L9 1" fill="none" stroke="#e63a35" stroke-width="2"/></svg>Automatic software patching</li>
        <li><svg width="9" height="9" viewBox="0 0 10 10"><path d="M1 5 L4 8 L9 1" fill="none" stroke="#e63a35" stroke-width="2"/></svg>Detailed monthly reports</li>
        <li><svg width="9" height="9" viewBox="0 0 10 10"><path d="M1 5 L4 8 L9 1" fill="none" stroke="#e63a35" stroke-width="2"/></svg>Optional onsite visits</li>
        <li><svg width="9" height="9" viewBox="0 0 10 10"><path d="M1 5 L4 8 L9 1" fill="none" stroke="#e63a35" stroke-width="2"/></svg>Happy, productive staff</li>
      </ul>
    </aside>
    <div class="monthly">
      <h3 class="section-title">MONTHLY SUPPORT PLAN OPTIONS</h3>
      <p class="body-copy">How much support does your business need? Choose the plan that suits your size and budget, each with remote help and clear response times, covered by our team.</p>
    </div>
    <div class="plans">
      <div class="plan"><div class="plan-badge">G</div><p>The Gold plan is ideal for small teams, with help desk support on weekdays.</p></div>
      <div class="plan"><div class="plan-badge">P</div><p>The Platinum plan adds onsite visits and extended support hours.</p></div>
      <div class="plan"><div class="plan-badge">P+</div><p>Platinum Plus offers full coverage, 24 hours a day, 7 days.</p></div>
    </div>
    <div class="people">
      <h3 class="section-title">PEOPLE MAKE THE DIFFERENCE</h3>
      <p class="body-copy">The heart of our business is our people. Our engineers are certified, friendly and focused on outcomes, giving you expert advice and support you can rely on.</p>
    </div>
    <div class="pricing">
      <h3 class="section-title">PRICING</h3>
      <p class="body-copy">Call us on 1300 482 615 to discuss your needs, and we will recommend the right plan for your business.</p>
    </div>
  </article>
</section>

</body>
</html>
```